KV HOLDING Business Cards

I need business cards for "KV Holding group LLC" doublesided... logo on the back (also include logo on front)
logo attached to project... i have jpg up..
Company Info:
827 North Cadwell Avenue, Suite 4B
Chicago, Illinois 60654
facsimile 312-481-2075 (list fax, address, website on all cards.)
www.kvholdinggroup.example
Three different people on cards:
Darnell P. Okafor, CPA MST
Principal
ofc 312-481-3900
mobile 312-204-7751
darnellpokafor@kvholdinggroup.example
Hollis T. Brennecke, CPA MST
Principal
hollistbrennecke@kvholdinggroup.example
mobile 708-539-1184
ofc 312-481-3900
Conrad M Pavlik
Principal
ofc 312-481-3900
no mobile
conradmpavlik@kvholdinggroup.example
I have multiple projects listed.. see below:
Business cards for amber gate ventures llc
letterhead
envelopes
Business cards for KV Holding LLC
letterhead
envelopes
Target Market(s)
rich people
Industry/Entity Type
Business
Look and feel
Each slider illustrates characteristics of the customer's brand and the style your logo design should communicate.

```html
<!DOCTYPE html>
<html lang="en">
<head>
<meta charset="utf-8">
<title>KV Holding Group LLC — Business Cards</title>
<link href="https://fonts.googleapis.com/css2?family=Cinzel:wght@500&family=Exo+2:wght@400;500&display=swap" rel="stylesheet">
<style>
  :root {
    --bg: #e9e7e3;
    --paper: #ffffff;
    --band-grey: #a7a7a7;
    --brand-blue: #1f4c8a;
    --panel-blue: #0f3f78;
    --panel-shade: #0a2f5c;
    --panel-light: #1b4f8e;
    --ink-light: #ffffff;
  }
  * { box-sizing: border-box; margin: 0; padding: 0; }
  html, body { width: 1200px; height: 658px; overflow: hidden; background: var(--bg); }
  .canvas { position: relative; width: 1200px; height: 658px; }

  .card {
    position: absolute;
    top: 170px;
    width: 555px;
    height: 317px;
    background: var(--paper);
    overflow: hidden;
    box-shadow: 0 6px 18px rgba(0,0,0,.18);
  }
  .card--back { left: 30px; }
  .card--front { left: 615px; }

  .brand {
    display: flex;
    align-items: center;
    gap: 10px;
    font-family: "Cinzel", serif;
    font-weight: 500;
    color: var(--brand-blue);
    white-space: nowrap;
  }
  .brand__dot { border-radius: 50%; background: var(--brand-blue); flex: none; }

  /* back */
  .back__band {
    position: absolute; left: 0; right: 0; top: 62px; height: 193px;
    background: var(--band-grey);
    display: flex; align-items: center; justify-content: center;
  }
  .card--back .brand { font-size: 27px; }
  .card--back .brand__dot { width: 18px; height: 18px; }

  /* front */
  .front__identity {
    position: absolute; left: 0; top: 0; width: 265px; height: 150px;
    display: flex; align-items: flex-end; justify-content: center; padding-bottom: 22px;
  }
  .card--front .brand { font-size: 16px; gap: 7px; }
  .card--front .brand__dot { width: 11px; height: 11px; }
  .front__address {
    position: absolute; left: 0; top: 150px; width: 265px; height: 88px;
    background: var(--band-grey);
    color: var(--ink-light);
    font-family: "Exo 2", sans-serif; font-size: 8.4px; line-height: 1.45;
    text-align: right; padding: 12px 12px 0 10px;
  }
  .front__people {
    position: absolute; left: 265px; top: 0; right: 0; bottom: 0;
    background: var(--panel-blue);
  }
  .front__people::before {
    content: ""; position: absolute; left: 0; right: 0; top: 150px; height: 88px;
    background: var(--panel-shade);
  }
  .front__people::after {
    content: ""; position: absolute; left: 0; right: 0; bottom: 0; height: 40px;
    background: var(--panel-light);
  }
  .person {
    position: absolute; right: 18px; z-index: 1;
    color: var(--ink-light); text-align: right;
    font-family: "Exo 2", sans-serif; font-size: 10px; line-height: 1.3;
  }
  .person__name { font-weight: 500; }
  .person--one { top: 26px; }
  .person--two { top: 118px; }
  .person--three { top: 206px; }
</style>
</head>
<body>
<main class="canvas">
  <section class="card card--back" aria-label="Card back">
    <div class="back__band">
      <div class="brand"><span class="brand__dot"></span><span>KV Holding Group LLC</span></div>
    </div>
  </section>

  <section class="card card--front" aria-label="Card front">
    <div class="front__identity">
      <div class="brand"><span class="brand__dot"></span><span>KV Holding Group LLC</span></div>
    </div>
    <address class="front__address" style="font-style:normal">
      827 North Cadwell Avenue, Suite 4B<br>
      Chicago, Illinois 60654<br>
      facsimile 312-481-2075 (list fax, address, website on all cards.)<br>
      www.kvholdinggroup.example
    </address>
    <div class="front__people">
      <div class="person person--one">
        <div class="person__name">Darnell P. Okafor, CPA MST</div>
        <div>Principal</div>
        <div>Ofc 312-481-3900</div>
        <div>Mobile 312-204-7751</div>
        <div>darnellpokafor@kvholdinggroup.example</div>
      </div>
      <div class="person person--two">
        <div class="person__name">Hollis T. Brennecke, CPA MST</div>
        <div>Principal</div>
        <div>hollistbrennecke@kvholdinggroup.example</div>
        <div>mobile 708-539-1184</div>
        <div>ofc 312-481-3900</div>
      </div>
      <div class="person person--three">
        <div class="person__name">Conrad M Pavlik</div>
        <div>Principal</div>
        <div>ofc 312-481-3900</div>
        <div>conradmpavlik@kvholdinggroup.example</div>
      </div>
    </div>
  </section>
</main>
</body>
</html>
```